Verpackungsdesign für Kaffeerösterei
Zielgruppe
wir Rösten Kaffee. Wir haben uns darauf Spezialisiert Hochwertigen Premium Caffe Crema herzustellen und bieten auch nur diesen in Unserem Shop www.brunovel-roest.de an. wir bieten 250gr. 500gr. Kaffee an. .
Es kann gerne verrückt oder anders sein, dennoch aber sehr edel.
die Zielgruppe ist weitgestreut, aber laut unserern Daten ist die Ideale Zielgruppe der 52 Jährige Mann, der Wert auf Hochwertige Genussmittel legt und auch bereit ist mehr Geld dafür zu bezahlen.
ich habe bereits ein beispiel design und die Druckvorlage bereitgestellt.
Aufgabenstellung
das Konzept unserer Internetseite sollte berücksichtigt werden, ansonsten ist dem Kreativen kopf keine Grenzen gesetzt.

```html
<!DOCTYPE html>
<html lang="de">
<head>
<meta charset="utf-8">
<title>Brunovel Cafe Crema – Verpackung 500g</title>
<link rel="stylesheet" href="https://fonts.googleapis.com/css2?family=Anton&family=Oswald:wght@500&display=swap">
<style>
  :root {
    --stage: #e6e6e6;
    --pack-white: #ffffff;
    --swirl-black: #000000;
    --swirl-grey: #8a8a8a;
    --label-pink: #e4007f;
    --label-ink: #2b1a1f;
    --badge-dark: #3a1d22;
  }
  html, body {
    margin: 0;
    padding: 0;
    width: 847px;
    height: 1200px;
    overflow: hidden;
    background: var(--stage);
  }
  .canvas {
    position: relative;
    width: 847px;
    height: 1200px;
  }
  .pack-front {
    position: absolute;
    left: 131px;
    top: 50px;
    width: 584px;
    height: 1100px;
    background: var(--pack-white);
    overflow: hidden;
  }
  .swirl-art {
    position: absolute;
    left: 0;
    top: 0;
    width: 584px;
    height: 1100px;
  }
  .product-label {
    position: absolute;
    left: 196px;
    top: 805px;
    width: 180px;
    height: 295px;
    background: var(--label-pink);
    color: var(--label-ink);
    text-align: center;
  }
  .brand-name {
    position: absolute;
    left: 0;
    right: 0;
    top: 46px;
    margin: 0;
    font-family: "Anton", sans-serif;
    font-size: 30px;
    line-height: 36px;
    letter-spacing: 1px;
  }
  .product-name {
    position: absolute;
    left: 0;
    right: 0;
    top: 110px;
    margin: 0;
    font-family: "Anton", sans-serif;
    font-size: 28px;
    line-height: 32px;
    letter-spacing: 0.5px;
  }
  .taste-note {
    position: absolute;
    left: 0;
    right: 0;
    top: 147px;
    margin: 0;
    font-family: "Oswald", sans-serif;
    font-weight: 500;
    font-size: 7.5px;
    line-height: 10px;
  }
  .handmade-seal {
    position: absolute;
    left: 66px;
    top: 174px;
    width: 48px;
    height: 48px;
    border-radius: 50%;
    background: var(--badge-dark);
  }
  .net-weight {
    position: absolute;
    left: 0;
    right: 0;
    top: 238px;
    margin: 0;
    font-family: "Oswald", sans-serif;
    font-weight: 500;
    font-size: 17px;
    line-height: 22px;
  }
</style>
</head>
<body>
<main class="canvas">
  <section class="pack-front">
    <svg class="swirl-art" viewBox="0 0 584 1100" role="img" aria-label="Schwarz-weiße Wirbelgrafik aus geschwungenen Streifen, die von oben links in die Fläche laufen">
      <defs>
        <radialGradient id="swirlTone" cx="0" cy="0.3" r="0.9">
          <stop offset="0" stop-color="var(--swirl-black)"/>
          <stop offset="0.55" stop-color="var(--swirl-grey)"/>
          <stop offset="1" stop-color="#dcdcdc"/>
        </radialGradient>
      </defs>
      <path d="M0 0 H584 V210 C430 200 330 250 295 300 C245 370 225 450 225 510 C225 650 120 790 0 860 Z" fill="url(#swirlTone)"/>
    </svg>

    <div class="product-label">
      <p class="brand-name">BRUNOVEL</p>
      <p class="product-name">CAFE CREMA</p>
      <p class="taste-note">Geschmacksnote: Dunkle Schokolade, karamell</p>
      <div class="handmade-seal" role="img" aria-label="Siegel"></div>
      <p class="net-weight">Net wt. 500g</p>
    </div>
  </section>
</main>
</body>
</html>
```